New Business Card Design Project

We require a business card design for Vexalund, a newly established Indian company.
Our focus is on the development, manufacturing, and export of a diverse array of pharmaceutical products on a global scale. The card should convey a professional appearance, as our primary markets are in Africa, China, and Southeast Asian nations.
We envision a two-sided business card, with the reverse side dedicated to a logo set against a solid color or an elegantly designed pattern. The corners should be rounded. We would appreciate seeing both horizontal and vertical design options. We trust the designer to utilize their expertise in creating this design.

The content for the business card is included in the attached Word file.

Target Market(s)

Our primary markets are in Africa, China, and Southeast Asian, Latin America, Maldives, Sri Lanka

Industry/Entity Type

Pharmaceutical Manufacturing and Export

Contact Information for Business Card

Colors

Designer to choose colors to be used in the design.

Requirements
Must have
• The reverse side of the business card features solely the logo along with the tagline, "Care for Every Day."
Should not have
• The logo should not exceed two instances, encompassing both the front and back sides of the card.

```html
<!DOCTYPE html>
<html lang="en">
<head>
<meta charset="utf-8">
<title>Vexalund Business Card</title>
<link rel="stylesheet" href="https://fonts.googleapis.com/css2?family=Poppins:wght@400;700&family=Open+Sans:wght@400&display=swap">
<style>
  :root {
    --stage: #232323;
    --brand-blue: #2fa7df;
    --card-dark: #202024;
    --accent-red: #ef5f4d;
    --ink-white: #ffffff;
  }
  * { margin: 0; padding: 0; box-sizing: border-box; }
  html, body { width: 1200px; height: 711px; overflow: hidden; background: var(--stage); }
  .canvas { position: relative; width: 1200px; height: 711px; background: var(--stage); }

  .card {
    position: absolute;
    width: 520px;
    height: 300px;
    border-radius: 22px;
    overflow: hidden;
  }

  /* Reverse side */
  .card-back {
    left: 60px; top: 60px;
    background: var(--brand-blue);
    display: flex; flex-direction: column; align-items: center; justify-content: center;
  }
  .brand-mark {
    display: flex; align-items: center; gap: 12px;
    font-family: "Poppins", sans-serif; font-weight: 700;
    white-space: nowrap;
  }
  .brand-mark .dot { border-radius: 50%; flex: none; }
  .card-back .brand-mark { font-size: 56px; color: var(--ink-white); line-height: 1; }
  .card-back .brand-mark .dot { width: 34px; height: 34px; background: var(--ink-white); }
  .tagline {
    margin-top: 16px;
    font-family: "Poppins", sans-serif; font-size: 13px; letter-spacing: 0.5px;
    color: var(--ink-white);
  }

  /* Front side */
  .card-front {
    left: 620px; top: 350px;
    background: var(--card-dark);
    border-bottom: 3px solid var(--brand-blue);
    border-left: 2px solid var(--brand-blue);
  }
  .name-block { position: absolute; left: 0; top: 34px; padding-left: 32px; }
  .name-bar { position: absolute; left: 0; top: 6px; width: 16px; height: 44px; background: var(--brand-blue); }
  .person-name { font-family: "Poppins", sans-serif; font-size: 24px; line-height: 1.1; white-space: nowrap; }
  .person-name .first { color: var(--brand-blue); font-weight: 700; }
  .person-name .last { color: var(--accent-red); font-weight: 400; }
  .person-role { font-family: "Open Sans", sans-serif; font-size: 13px; color: var(--ink-white); margin-top: 2px; }

  .card-front .brand-mark { position: absolute; right: 34px; top: 30px; font-size: 38px; color: var(--brand-blue); line-height: 1; }
  .card-front .brand-mark .dot { width: 22px; height: 22px; background: var(--brand-blue); }

  .contact-list {
    position: absolute; right: 26px; top: 150px;
    list-style: none;
    font-family: "Open Sans", sans-serif; font-size: 13px; color: var(--ink-white);
  }
  .contact-list li { display: flex; align-items: center; justify-content: flex-end; gap: 9px; height: 21px; white-space: nowrap; }
  .contact-list svg { width: 13px; height: 13px; flex: none; }

  .address {
    position: absolute; left: 32px; bottom: 30px;
    font-family: "Open Sans", sans-serif; font-size: 13px; line-height: 1.45; color: var(--ink-white);
  }
</style>
</head>
<body>
<main class="canvas">

  <section class="card card-back" aria-label="Card reverse">
    <div class="brand-mark"><span class="dot"></span><span>Vexalund</span></div>
    <p class="tagline">Care for Every Day.</p>
  </section>

  <section class="card card-front" aria-label="Card front">
    <div class="name-block">
      <span class="name-bar"></span>
      <h1 class="person-name"><span class="first">Rohan</span> <span class="last">K. Malvi</span></h1>
      <p class="person-role">CEO</p>
    </div>

    <div class="brand-mark"><span class="dot"></span><span>Vexalund</span></div>

    <ul class="contact-list">
      <li>+91 73581 06497
        <svg viewBox="0 0 14 14" aria-hidden="true"><rect x="3" y="1" width="8" height="12" rx="1.5" fill="none" stroke="var(--accent-red)" stroke-width="1.5"/></svg>
      </li>
      <li>www.vexalund.com
        <svg viewBox="0 0 14 14" aria-hidden="true"><circle cx="7" cy="7" r="6" fill="none" stroke="var(--brand-blue)" stroke-width="1.4"/><path d="M1 7h12M7 1c-3 3-3 9 0 12M7 1c3 3 3 9 0 12" fill="none" stroke="var(--brand-blue)" stroke-width="1"/></svg>
      </li>
      <li>rmalvi@vexalund.com
        <svg viewBox="0 0 14 14" aria-hidden="true"><rect x="1" y="3" width="12" height="9" rx="1" fill="var(--accent-red)"/><path d="M1.5 3.5 7 8l5.5-4.5" fill="none" stroke="var(--card-dark)" stroke-width="1.2"/></svg>
      </li>
    </ul>

    <p class="address">7, Sunrise Colony,<br>Nandipur, 440210, India</p>
  </section>

</main>
</body>
</html>
```